Exciting opportunity to create logo and a label for our natural health brand.

About us

We are a customer centric health supplement brand who believes in natural medicine and high quality ingredients. We take a holistic approach to healthcare, with an eastern philosophy. We believe in being partners with our customers in their health care journey and are invested in their well being.

Our brand philosophy and values are attached (see Vorna philosophy.png). Our personality traits are:

- Natural
- Fresh
- Modern
- Balanced (in a holistic sense)

Task breakdown

1. Design a fresh feeling logo for us
- We want it to represent our values and high quality ingredients. We would like the quality of the product to be reflected in the branding and have a high end feel.
- Logo text must include Vorna Health Sciences
- We want the Vorna to be the focus of the logo (see uploaded image Vorna logo example.png)
The logo does not have to follow this layout, but we just want the Vorna to stand out. Feel free to use your creative license on this!

2. Create an attractive label to go on the supplement bottle
- The designs need to be eye catching, give a sense of high end ingredients and natural products and tie in with the logo to give a joined up feel.
- We are selling our products online and need them to really stand out from the competition.
- See examples of labels and packaging we like (1 -7 label design).

The initial label we would like you to design would be for our product Calm Drift. It is a product that assists in the management of Anxiety and stress. The label will appear on the bottle that holds the capsules for this supplement, see uploaded files (Example plain bottles.png). The bottles may be white as the picture shows or dark blue recyclable plastic or dark brown glass . We don't have the exact dimensions of the bottle yet, but I will follow up with these.

The label needs to include the following things:
1. The logo
2. The name of the product
3. The product is to help with the relief of Anxiety and Stress
4. Number of capsules the bottle contains
5. The back of the label should have
i) The ingredients
ii) Dosage
iii) Directions of use

Please use placeholder text where needed.

We look forward to seeing your design. Thank you.

```html
<!DOCTYPE html>
<html lang="en">
<head>
<meta charset="utf-8">
<title>Vorna Health Sciences – Calm Drift Label</title>
<link href="https://fonts.googleapis.com/css2?family=Oswald:wght@500&family=Montserrat:wght@400;500;700&family=Roboto+Condensed:wght@300;400;700&family=Allura&display=swap" rel="stylesheet">
<style>
  :root{
    --sage-light:#e6ede0;
    --sage:#d6e1cf;
    --sage-band:#9db497;
    --forest:#2e5a36;
    --forest-text:#2f6b3a;
    --ink:#2b2b2b;
    --white:#ffffff;
  }
  *{margin:0;padding:0;box-sizing:border-box}
  html,body{width:1200px;height:1200px;overflow:hidden;background:var(--white)}
  .canvas{position:relative;width:1200px;height:1200px}

  .label{position:absolute;background:linear-gradient(90deg,var(--sage) 0%,var(--sage-light) 45%,var(--sage) 100%);overflow:hidden}

  /* front */
  .front{left:60px;top:300px;width:500px;height:595px}
  .brand{position:absolute;top:70px;left:0;width:100%;text-align:center;color:var(--ink);font-family:"Montserrat",sans-serif;font-weight:500}
  .brand-name{font-size:62px;line-height:1;letter-spacing:2px}
  .brand-sub{font-size:14px;letter-spacing:3px;margin-top:8px}
  .brand-dot{display:inline-block;width:8px;height:8px;border-radius:50%;background:var(--ink);margin-right:8px;vertical-align:middle}
  .product-name{position:absolute;top:308px;width:100%;text-align:center;font-family:"Oswald",sans-serif;font-weight:500;font-size:70px;letter-spacing:1px;color:var(--ink)}
  .benefit-band{position:absolute;top:420px;left:0;width:100%;height:44px;background:var(--sage-band);color:var(--white);font-family:"Montserrat",sans-serif;font-size:19px;letter-spacing:2px;text-align:center;line-height:44px}
  .benefit-band b{font-weight:700}
  .rule{position:absolute;top:485px;left:105px;width:290px;height:2px;background:var(--forest)}
  .pillars{position:absolute;top:498px;width:100%;text-align:center;font-family:"Allura",cursive;font-size:30px;color:var(--ink)}
  .count-band{position:absolute;top:547px;left:0;width:100%;height:42px;background:var(--forest);color:var(--white);font-family:"Montserrat",sans-serif;font-size:18px;letter-spacing:2.5px;text-align:center;line-height:42px}

  /* back */
  .back-left{left:620px;top:300px;width:250px;height:595px;border-radius:0 8px 0 0}
  .back-right{left:890px;top:300px;width:250px;height:595px;border-radius:8px 0 0 0;display:flex;flex-direction:column}
  .facts-box{position:absolute;left:0;top:17px;width:220px;height:290px;background:var(--white);border:2px solid var(--ink);border-left:none}
  .facts-title{font-family:"Roboto Condensed",sans-serif;font-weight:700;font-size:14px;color:var(--ink);padding:14px 0 0 20px}
  .small{font-family:"Roboto Condensed",sans-serif;font-size:14px;color:var(--ink);line-height:1.4}
  .ingredients{position:absolute;left:8px;top:322px;width:232px}
  .maker{position:absolute;left:8px;top:388px;width:232px}
  .barcode-space{position:absolute;left:0;top:463px;width:222px;height:82px;background:var(--white)}
  .web-band{position:absolute;left:0;bottom:0;width:100%;height:42px;background:var(--forest);color:var(--white);font-family:"Roboto Condensed",sans-serif;font-size:14px;line-height:42px;padding-left:12px}
  .back-right .web-band{text-align:right;padding-right:12px}

  .back-content{flex:1;display:flex;flex-direction:column;gap:8px;padding:18px 10px 50px 18px;font-family:"Roboto Condensed",sans-serif;font-size:13.5px;line-height:1.35;color:var(--ink)}
  .directions p+p{margin-top:8px}
  .directions .lead{color:var(--forest-text);font-weight:700}
  .divider{height:2px;background:var(--forest);flex:none}
  .caution{color:var(--forest-text);letter-spacing:.4px;text-transform:uppercase}
  .disclaimer{background:var(--sage-band);padding:5px 8px}
</style>
</head>
<body>
<div class="canvas">

  <section class="label front">
    <div class="brand">
      <div class="brand-name">Vorna</div>
      <div class="brand-sub"><span class="brand-dot"></span>HEALTH SCIENCES</div>
    </div>
    <h1 class="product-name">CALM DRIFT</h1>
    <div class="benefit-band">RELIEF OF <b>ANXIETY</b> AND <b>STRESS</b></div>
    <div class="rule"></div>
    <div class="pillars">Vitamins · Minerals · Herbs</div>
    <div class="count-band">60 CAPSULES | DIETARY SUPPLEMENT</div>
  </section>

  <section class="label back-left">
    <div class="facts-box"><div class="facts-title">SUPPLEMENT FACTS</div></div>
    <p class="small ingredients"><b>INGREDIENTS:</b> Lorem ipsum dolor sit amet, consectetuer adipiscing elit, sed diam</p>
    <p class="small maker"><b>MANUFACTURER:</b><br>VORNA HEALTH SCIENCES</p>
    <div class="barcode-space"></div>
    <div class="web-band">www.vornahealthsciences.com</div>
  </section>

  <section class="label back-right">
    <div class="back-content">
      <div class="directions">
        <p><span class="lead">SUGGESTED USE:</span> As a dietary supplement, take one capsule twice daily, preferably with meals.</p>
        <p><span class="lead">WARNING:</span> If you are pregnant or breastfeeding, do not use this product. If symptoms persist or worsen, or if new symptoms develop, discontinue use and consult a health care practitioner. If you are taking prescription medications, consult a health care practitioner prior to use. Consumption with alcohol, other drugs or natural health products with sedative properties is not recommended.</p>
      </div>
      <div class="divider"></div>
      <div class="caution">Keep out of reach of children. Do not use if safety seal is damaged or missing. Store in a cool, dry place.</div>
      <div class="divider"></div>
      <div class="disclaimer">These products have not been evaluated by the FDA and are not intended to diagnose, treat, cure, or prevent any disease.</div>
    </div>
    <div class="web-band">www.vornahealthsciences.com</div>
  </section>

</div>
</body>
</html>
```